Ancient Art and Artifact information website

Hello Designers,
We are starting up a new website who talk abut and discusses an ancient arts artifacts. We would covering a wide range of countries ranging from Egypt, Greece, India, Syria, Rome, etc. My website name Bright Loom
Designs that fits with ancient theme and some kind of uniqueness would be accepted.
Requirements:
1) A home page design
2) Sub page design
3) A suitable logo
Sections can be added are featured ancient arts/places with short description followed by a more button, latest news, and comment section.
Add contents if you found relevant for this category of website. Ability to share the information through social media is desired.
Must be a responsive design. I look forward to designs which are mind blowing.
Number of Pages Required
2 page

```html
<!DOCTYPE html>
<html lang="en">
<head>
<meta charset="utf-8">
<title>Bright Loom — Ancient Arts</title>
<link href="https://fonts.googleapis.com/css2?family=Montserrat:wght@700;800&family=Open+Sans:wght@400;600;700&family=Roboto+Condensed:wght@400;700&display=swap" rel="stylesheet">
<style>
:root{
  --gold:#d9a440;
  --gold-soft:#e3b458;
  --gold-dark:#c68f2c;
  --ink:#2a2a2a;
  --text:#555;
  --white:#fff;
  --grey-card:#d6d6d6;
  --brown-1:#5e3c14;
  --brown-2:#a9782f;
}
*{box-sizing:border-box;margin:0;padding:0}
html,body{width:1200px;height:2503px;overflow:hidden}
body{position:relative;font-family:"Open Sans",sans-serif;color:var(--text);background:var(--white)}
.abs{position:absolute}

/* header */
.site-header{position:absolute;top:0;left:0;width:1200px;height:93px;background:var(--white);border-bottom:3px solid var(--gold)}
.brand{position:absolute;left:98px;top:32px;font-family:"Montserrat",sans-serif;font-weight:800;font-size:29px;color:var(--ink);letter-spacing:.5px}
.main-nav{position:absolute;left:414px;top:40px;display:flex}
.main-nav a{font-size:13px;color:#444;text-decoration:none;text-transform:uppercase;margin-right:36px;position:relative}
.main-nav a.active{color:var(--gold)}
.main-nav a.active::after{content:"";position:absolute;left:50%;top:39px;margin-left:-9px;border:9px solid transparent;border-bottom-color:var(--gold);border-top:0}
.sign-in{position:absolute;left:1016px;top:29px;width:86px;height:38px;border:1.5px solid #444;border-radius:10px;font-size:13px;font-weight:600;color:#333;text-align:center;line-height:35px;text-transform:uppercase}

/* hero */
.hero{position:absolute;top:96px;left:0;width:1200px;height:530px;background:
  radial-gradient(ellipse at 12% 55%,rgba(120,80,35,.55) 0%,transparent 45%),
  radial-gradient(ellipse at 88% 55%,rgba(120,80,35,.55) 0%,transparent 45%),
  linear-gradient(180deg,#5b8dbf 0%,#9fb8cc 22%,#b89262 45%,#a57a45 75%,#d9c3a0 100%)}
.hero-title{position:absolute;top:168px;width:100%;text-align:center;font-family:"Roboto Condensed",sans-serif;font-weight:700;font-size:52px;color:var(--white);text-shadow:0 2px 6px rgba(0,0,0,.35)}
.hero-sub{position:absolute;top:247px;width:100%;text-align:center;font-size:17px;color:var(--white);text-shadow:0 1px 3px rgba(0,0,0,.4)}
.hero-btn{position:absolute;left:542px;top:300px;width:116px;height:44px;border:1.5px solid var(--white);border-radius:8px;color:var(--white);font-size:13px;text-align:center;line-height:41px;background:rgba(0,0,0,.15)}
.dots{position:absolute;top:484px;left:560px;display:flex;gap:6px}
.dots span{display:block;width:11px;height:11px;border:1.5px solid var(--white);border-radius:50%}
.dots span.on{background:var(--gold)}

/* about */
.about-title{left:98px;top:684px;font-family:"Roboto Condensed",sans-serif;font-weight:400;font-size:28px;color:var(--ink)}
.about-text{left:98px;top:738px;width:570px;font-size:12px;line-height:25.5px;color:#555}
.btn-outline{border:1.5px solid var(--gold);border-radius:10px;color:var(--gold);font-size:12px;text-transform:uppercase;text-align:center}
.about-btn{left:98px;top:888px;width:108px;height:38px;line-height:35px}
.about-media{left:703px;top:694px;width:400px;height:232px;border:3px solid #ddd;background:linear-gradient(180deg,#8ab3d8 0%,#c2d3df 35%,#b9875a 55%,#d4b38d 100%)}
.play{position:absolute;left:180px;top:100px;width:36px;height:28px;border-radius:6px;background:var(--gold)}
.play::after{content:"";position:absolute;left:14px;top:8px;border-left:11px solid var(--white);border-top:6px solid transparent;border-bottom:6px solid transparent}

/* featured */
.featured{position:absolute;top:993px;left:0;width:1200px;height:614px;background:
  radial-gradient(ellipse 260px 180px at 18% 20%,rgba(60,35,10,.35),transparent 70%),
  radial-gradient(ellipse 300px 200px at 80% 80%,rgba(60,35,10,.35),transparent 70%),
  radial-gradient(ellipse 220px 160px at 60% 15%,rgba(210,160,80,.25),transparent 70%),
  radial-gradient(ellipse 240px 170px at 30% 85%,rgba(210,160,80,.2),transparent 70%),
  radial-gradient(ellipse at 45% 45%,var(--brown-2) 0%,#86591f 55%,var(--brown-1) 100%)}
.section-title{position:absolute;width:100%;text-align:center;font-family:"Roboto Condensed",sans-serif;font-weight:400;font-size:35px}
.rule{position:absolute;left:574px;width:52px;height:3px}
.featured .section-title{top:58px;color:var(--white)}
.featured .rule{top:124px;background:var(--white)}
.art{position:absolute;top:192px;width:360px;text-align:center;color:var(--white)}
.art-photo{width:234px;height:234px;margin:0 auto;border-radius:50%;border:4px solid var(--white);background:linear-gradient(180deg,#3f7fc7 0%,#7fb0de 45%,#c9904a 60%,#b27736 100%)}
.art h3{margin-top:26px;font-family:"Roboto Condensed",sans-serif;font-size:21px;font-weight:700}
.art p{margin-top:10px;font-size:12px;line-height:22px;padding:0 26px}
.art .more{margin-top:10px;font-size:12px;font-weight:700}
.arrow-w{position:absolute;top:282px;color:var(--white);font-size:26px}

/* news */
.news .section-title{top:1666px;color:var(--ink)}
.news-rule{top:1725px;background:var(--gold)}
.news-card{position:absolute;top:1780px;width:247px;height:315px;background:
  radial-gradient(ellipse at 30% 30%,rgba(240,190,100,.5),transparent 60%),
  radial-gradient(ellipse at 75% 80%,rgba(170,115,35,.4),transparent 60%),var(--gold);transform:perspective(600px) rotateY(8deg)}
.news-inner{position:absolute;left:20px;top:20px;width:208px;height:276px;background:var(--white);padding:10px}
.news-photo{width:188px;height:140px;background:linear-gradient(180deg,#7aa4cf 0%,#a9b6bd 40%,#7d7262 100%)}
.news-photo.stone{background:linear-gradient(180deg,#9a9a98 0%,#bdbdb8 50%,#6f6f6b 100%)}
.news-inner h4{margin-top:16px;font-size:13px;color:#222;font-weight:600}
.news-inner p{margin-top:4px;font-size:11.5px;line-height:17px;color:#666}
.news-inner .more{position:absolute;right:22px;bottom:22px;font-size:10px;color:var(--gold)}
.comments{position:absolute;top:1780px;width:248px;height:315px;background:
  radial-gradient(ellipse at 20% 25%,rgba(255,255,255,.35),transparent 55%),
  radial-gradient(ellipse at 80% 70%,rgba(150,150,150,.3),transparent 55%),var(--grey-card);padding:28px 20px;transform:perspective(600px) rotateY(-8deg)}
.comments h5{font-size:14px;font-weight:600;color:#333;margin-bottom:12px}
.c-item{margin-bottom:14px}
.c-item .t{font-size:10.5px;color:var(--gold);font-weight:600}
.c-item .s{font-size:9px;color:#888;font-style:italic;margin:2px 0 3px 15px}
.c-item .b{font-size:12px;color:#444;line-height:18px;margin-left:15px}
.c-item .m{font-size:10px;color:var(--gold);margin:4px 0 0 15px}
.c-item .m span{color:#777;margin-left:6px}
.arrow-g{position:absolute;top:1920px;color:var(--gold);font-size:24px}

/* footer */
.site-footer{position:absolute;top:2166px;left:0;width:1200px;height:337px;background:
  radial-gradient(ellipse 300px 120px at 20% 30%,rgba(255,220,150,.3),transparent 70%),
  radial-gradient(ellipse 320px 130px at 70% 75%,rgba(180,125,40,.3),transparent 70%),
  radial-gradient(ellipse 260px 110px at 90% 20%,rgba(180,125,40,.22),transparent 70%),
  linear-gradient(180deg,var(--gold-soft),var(--gold))}
.f-col{position:absolute;top:46px;color:var(--white)}
.f-col h6{font-size:17px;font-weight:700;text-transform:uppercase;margin-bottom:18px}
.f-col li{list-style:none;font-size:12px;margin-bottom:11px}
.f-col li::before{content:"» ";margin-right:4px}
.contact li{display:flex;gap:12px;line-height:20px;margin-bottom:18px}
.contact li::before{content:none}
.contact svg{flex:none;margin-top:3px}
.field{width:270px;height:38px;background:#f5ead6;border-radius:3px;margin-bottom:9px;font-size:12px;color:#666;padding:11px 16px}
.submit{width:96px;height:38px;background:#2e2e2e;color:var(--white);font-size:12px;font-weight:700;text-align:center;line-height:38px;border-radius:3px}
.f-base{position:absolute;left:0;top:2445px;width:1200px;height:1px;background:rgba(255,255,255,.35)}
.socials{position:absolute;left:96px;top:2458px;display:flex;gap:8px}
.socials span{display:block;width:25px;height:25px;border:2px solid var(--white);border-radius:50%}
.copy{position:absolute;left:878px;top:2463px;font-size:12px;color:var(--white)}
</style>
</head>
<body>

<header class="site-header">
  <div class="brand">BRIGHT LOOM</div>
  <nav class="main-nav">
    <a class="active">Home</a><a>About Us</a><a>Featured Arts</a><a>News</a><a>Testimonials</a><a>Contact Us</a>
  </nav>
  <div class="sign-in">Sign In</div>
</header>

<section class="hero" role="img" aria-label="Temple courtyard lined with carved stone pharaoh statues under a blue sky">
  <h1 class="hero-title">WELCOME TO BRIGHT LOOM</h1>
  <p class="hero-sub">We are starting up a new website who talk about and discusses an ancient arts artifacts</p>
  <div class="hero-btn">READ MORE</div>
  <div class="dots"><span class="on"></span><span></span><span></span><span></span><span></span></div>
</section>

<h2 class="abs about-title">About Bright Loom</h2>
<p class="abs about-text">Lorem Ipsum has been the industry's standard dummy text ever since the 1500s, when an unknown printer took a galley of type and scrambled it to make a type specimen book. It has survived not only five centuries, but also the leap into electronic typesetting, remaining essentially unchanged. It was popularised in the 1960s with the release of Letraset sheets containing Lorem Ipsum passages, and more recently with desktop publishin versions of Lorem Ipsum.</p>
<div class="abs btn-outline about-btn">Read More</div>
<div class="abs about-media" role="img" aria-label="Video still of an avenue of stone sphinx statues"><span class="play"></span></div>

<section class="featured" role="region" aria-label="Featured Ancient Arts">
  <h2 class="section-title">Featured Ancient Arts</h2>
  <div class="rule"></div>
  <span class="arrow-w" style="left:66px">‹</span>
  <span class="arrow-w" style="left:1118px">›</span>
  <div class="art" style="left:59px">
    <div class="art-photo" role="img" aria-label="Colonnade of carved temple statues"></div>
    <h3>Lorem Ipsum</h3>
    <p>Lorem Ipsum is that it has a more-or-less normal distribution of letters, as Content here,</p>
    <div class="more">READ MORE ➜</div>
  </div>
  <div class="art" style="left:416px">
    <div class="art-photo" role="img" aria-label="Great stone sphinx against a blue sky"></div>
    <h3>Finibus Bonorum</h3>
    <p>Lorem Ipsum is that it has a more-or-less normal distribution of letters, as Content here,</p>
    <div class="more">READ MORE ➜</div>
  </div>
  <div class="art" style="left:780px">
    <div class="art-photo" role="img" aria-label="Stepped pyramid in the desert"></div>
    <h3>Lorem ipsum dolor</h3>
    <p>Lorem Ipsum is that it has a more-or-less normal distribution of letters, as Content here,</p>
    <div class="more">READ MORE ➜</div>
  </div>
</section>

<section class="news">
  <h2 class="section-title">Latest News</h2>
  <div class="rule news-rule"></div>
  <span class="arrow-g" style="left:58px">‹</span>
  <span class="arrow-g" style="left:1126px">›</span>

  <article class="news-card" style="left:98px">
    <div class="news-inner">
      <div class="news-photo" role="img" aria-label="Ruins of a columned temple on a hill"></div>
      <h4>PRO EA SUAS ERAN</h4>
      <p>Ad nemore docendi nec, ut qui errem torquatos, ex mea vidit neglegentur.</p>
      <span class="more">READ MORE &gt;&gt;</span>
    </div>
  </article>
  <aside class="comments" style="left:350px">
    <h5>COMMENTS</h5>
    <div class="c-item"><div class="t">➜ EI PROBO UTAMUR PROBO</div><div class="s">Numquam epicuri mel at duo at apicur</div><div class="b">Ei probo utamur volumus his, has probo utamur volumus his, has</div><div class="m">💬 4 comments <span>★★★★</span></div></div>
    <div class="c-item"><div class="t">➜ EI PROBO UTAMUR PROBO</div><div class="s">Numquam epicuri mel at duo at apicur</div><div class="b">Ei probo utamur volumus his, has probo utamur volumus his, has</div><div class="m">💬 4 comments <span>★★★★</span></div></div>
  </aside>

  <article class="news-card" style="left:602px">
    <div class="news-inner">
      <div class="news-photo stone" role="img" aria-label="Carved marble relief sculpture"></div>
      <h4>LOREM IPSUM DOLOR</h4>
      <p>Ad nemore docendi nec, ut qui errem torquatos, ex mea vidit neglegentur.</p>
      <span class="more">READ MORE &gt;&gt;</span>
    </div>
  </article>
  <aside class="comments" style="left:855px">
    <h5>COMMENTS</h5>
    <div class="c-item"><div class="t">➜ EI PROBO UTAMUR PROBO</div><div class="s">Numquam epicuri mel at duo at apicur</div><div class="b">Ei probo utamur volumus his, has probo utamur volumus his, has</div><div class="m">💬 4 comments <span>★★★★</span></div></div>
    <div class="c-item"><div class="t">➜ EI PROBO UTAMUR PROBO</div><div class="s">Numquam epicuri mel at duo at apicur</div><div class="b">Ei probo utamur volumus his, has probo utamur volumus his, has</div><div class="m">💬 4 comments <span>★★★★</span></div></div>
  </aside>
</section>

<footer class="site-footer">
  <div class="f-col contact" style="left:98px">
    <h6>Contact Us</h6>
    <ul>
      <li><svg width="14" height="13" viewBox="0 0 14 13"><path d="M7 0 0 6h2v7h4V9h2v4h4V6h2z" fill="#fff"/></svg><span>208 Loomhall Lane, Ardenvale<br>North District</span></li>
      <li><svg width="10" height="15" viewBox="0 0 10 15"><rect x="1" y="1" width="8" height="13" rx="1.5" fill="none" stroke="#fff" stroke-width="1.6"/><circle cx="5" cy="11.5" r="1" fill="#fff"/></svg><span>Call Us : (555) 014-2290</span></li>
      <li><svg width="15" height="11" viewBox="0 0 15 11"><rect x="1" y="1" width="13" height="9" fill="none" stroke="#fff" stroke-width="1.5"/><path d="M1 1l6.5 5L14 1" fill="none" stroke="#fff" stroke-width="1.5"/></svg><span>hello@brightloom.example</span></li>
    </ul>
  </div>
  <div class="f-col" style="left:394px">
    <h6>Quick Links</h6>
    <ul><li>Home</li><li>About us</li><li>Featured Arts</li><li>Latest News</li><li>Contact us</li></ul>
  </div>
  <div class="f-col" style="left:604px">
    <h6>Other Links</h6>
    <ul><li>Site map</li><li>Terms and Conditions</li><li>Disclaimer</li><li>Privacy Policy</li><li>Contact us</li></ul>
  </div>
  <div class="f-col" style="left:828px">
    <h6>Contact Form</h6>
    <div class="field" style="margin-left:4px">Enter Name</div>
    <div class="field" style="margin-left:4px">Enter Email</div>
    <div class="submit" style="margin-left:4px">SUBMIT</div>
  </div>
</footer>
<div class="f-base"></div>
<div class="socials" aria-label="Social links"><span></span><span></span><span></span><span></span></div>
<div class="copy">© &nbsp;Bright Loom 2017 . All Rights Reserved</div>
</body>
</html>
```